Design (no text) for 7 pages of Wordpress website

I need seven of the pages on a website re-designed. The website is using Wordpress as the platform.

The text on the pages can remain unchanged.

The site is for outdoor markets, events.

Industry/Entity Type

Events, markets, fairs

Number of Pages Required

5+ page

Colors
00AB8E
00BBA5
67D7C9
C6EFE9
E9F9F6
EE7325
F08F49
F5BC92
FAE3D3
FDF4ED

```html
<!DOCTYPE html>
<html lang="en">
<head>
<meta charset="utf-8">
<title>Gumleaf Gully Markets – Pages</title>
<link rel="stylesheet" href="https://fonts.googleapis.com/css2?family=Oswald:wght@300;400;600;700&family=Roboto:wght@400;500;700&display=swap">
<style>
:root{
  --teal-dark:#00AB8E;
  --teal:#00BBA5;
  --teal-mid:#67D7C9;
  --teal-pale:#C6EFE9;
  --teal-wash:#E9F9F6;
  --orange:#EE7325;
  --orange-mid:#F08F49;
  --orange-pale:#F5BC92;
  --ink:#111;
  --text:#5f5f5f;
  --dark:#262626;
  --sheet:#b4b4b4;
  --white:#fff;
}
*{box-sizing:border-box;margin:0;padding:0}
html,body{width:1200px;height:3559px;overflow:hidden}
body{background:var(--sheet);font-family:'Roboto',sans-serif;color:var(--text);position:relative}
.page{position:absolute;left:133px;width:934px;background:var(--white);overflow:hidden}
.page--landing{top:126px;height:620px}
.page--visitors{top:834px;height:2598px}

/* top bar */
.topbar{height:28px;background:var(--teal);color:var(--white);font-size:10.5px;font-weight:500;display:flex;align-items:center;padding:0 87px;justify-content:space-between;white-space:nowrap}
.topbar span{display:inline-flex;align-items:center;gap:5px}
.topbar .contact{display:flex;gap:34px}
.topbar svg{width:10px;height:10px;fill:var(--white)}

/* header */
.header{height:75px;display:flex;align-items:center;padding:0 87px;justify-content:space-between;background:var(--white);white-space:nowrap}
.brand{flex:none;display:flex;align-items:center;gap:6px;font-family:'Oswald',sans-serif;font-weight:600;font-size:16px;color:var(--ink);letter-spacing:.3px;margin-right:24px}
.brand i{width:11px;height:11px;background:var(--orange);display:block}
.nav{display:flex;gap:15px;font-size:11.6px;font-weight:500;color:var(--ink);align-items:center;flex:none}
.nav a{color:inherit;text-decoration:none;position:relative;white-space:nowrap}
.nav .active{color:var(--orange)}
.nav .active::before{content:"";position:absolute;left:50%;bottom:-9px;width:30px;height:3px;margin-left:-20px;background:var(--orange)}
.caret::after{content:"";display:inline-block;margin-left:5px;border:4px solid transparent;border-top:5px solid currentColor;vertical-align:-2px}
.nav svg{width:11px;height:11px;flex:none}

/* scallops */
.scallop{position:absolute;left:0;width:100%;height:10px;background-size:13px 10px;background-repeat:repeat-x}
.scallop--down-wash{background-image:radial-gradient(circle at 50% 0,var(--teal-wash) 6px,transparent 6.6px)}
.scallop--down-white{background-image:radial-gradient(circle at 50% 100%,var(--white) 6px,transparent 6.6px)}
.scallop--down-teal{background-image:radial-gradient(circle at 50% 0,var(--teal) 6px,transparent 6.6px)}
.scallop--up-wash{background-image:radial-gradient(circle at 50% 100%,var(--teal-wash) 6px,transparent 6.6px)}

/* landing hero */
.chooser{position:relative;height:221px;background:var(--teal-wash);text-align:center}
.chooser h1{padding-top:54px;font-family:'Oswald',sans-serif;font-size:19px;color:var(--ink);font-weight:300;letter-spacing:.2px}
.chooser h1 b,.section-title b,.visitor-hero h1 b{font-weight:600}
.chooser .buttons{display:flex;justify-content:center;gap:23px;margin-top:24px}
.pill{width:196px;height:40px;border-radius:20px;display:flex;align-items:center;color:var(--white);font-weight:700;font-size:13.5px;padding:3px;text-decoration:none}
.pill i{width:34px;height:34px;border-radius:50%;background:var(--white);display:block;flex:none}
.pill span{flex:1;text-align:center;padding-right:30px}
.pill--visitors{background:var(--orange)}
.pill--stall{background:var(--teal)}
.chooser .scallop{bottom:-10px;z-index:2}

/* footer */
.footer{position:relative;background:var(--dark);color:#ddd;height:297px;font-size:10.5px}
.footer-cols{position:absolute;top:50px;left:0;right:0;height:170px}
.footer .f-brand{position:absolute;left:100px;top:33px;font-family:'Oswald',sans-serif;font-weight:600;font-size:15px;color:var(--white);display:flex;gap:5px;align-items:center}
.footer .f-brand i{width:10px;height:10px;background:var(--orange);display:block}
.footer .socials{position:absolute;left:94px;top:95px;display:flex;gap:13px}
.footer .socials i{width:10px;height:10px;border-radius:50%;background:var(--white);display:block}
.footer h4{font-size:12.5px;font-weight:700;color:var(--white);margin-bottom:17px}
.f-office{position:absolute;left:249px;top:0}
.f-office .row{display:flex;gap:10px;margin-bottom:13px;line-height:15px}
.f-office .row svg{width:11px;height:11px;fill:var(--teal);margin-top:1px;flex:none}
.f-office small{display:block;font-size:9px;font-weight:700;color:var(--white)}
.f-company{position:absolute;left:517px;top:0}
.f-company a{display:block;color:#ddd;text-decoration:none;line-height:20px}
.f-quote{position:absolute;left:672px;top:0;width:200px}
.f-quote p{font-size:9.5px;line-height:14px;margin-bottom:14px}
.btn-quote{display:block;width:154px;height:31px;border-radius:16px;background:var(--orange);color:var(--white);text-align:center;line-height:31px;font-weight:700;font-size:11.5px}
.footer .rule{position:absolute;left:87px;right:87px;top:233px;border-top:1px solid #555}
.goup{position:absolute;right:87px;top:226px;width:62px;height:14px;border-radius:7px;background:var(--teal);color:var(--white);font-size:8.5px;font-weight:700;text-align:center;line-height:14px}
.footer .legal{position:absolute;left:87px;right:87px;top:258px;display:flex;justify-content:space-between;font-size:10px}
.legal nav{display:flex;gap:8px}
.legal nav a{color:#ddd;text-decoration:none}

/* visitors */
.visitor-hero{position:relative;height:360px;background:linear-gradient(135deg,#7a4848 0%,#4e5360 40%,#6b6a6c 70%,#8b8a92 100%);display:flex;align-items:center;justify-content:center}
.visitor-hero h1{color:var(--white);font-family:'Oswald',sans-serif;font-weight:300;font-size:26px;letter-spacing:.2px}
.visitor-hero .scallop{bottom:0}
.intro{position:relative;height:589px}
.intro .copy{position:absolute;left:87px;top:102px;width:350px}
.h2{font-family:'Oswald',sans-serif;font-weight:700;font-size:22px;color:var(--ink);letter-spacing:.3px}
.copy p{font-size:10.8px;line-height:18.6px;margin-top:7px}
.copy .h2+p{margin-top:26px}
.copy a{color:var(--orange);font-weight:700;text-decoration:none}
.copy p.lead{color:var(--ink);font-weight:500}
.photo{position:absolute}
.intro .photo{left:481px;top:81px;width:367px;height:422px;background:linear-gradient(180deg,#4d5a3a 0%,#6a7356 35%,#7d7f86 65%,#5e5f63 100%)}
.expect{position:relative;height:500px;background:var(--teal-wash)}
.expect .scallop{top:-10px}
.section-title{text-align:center;font-family:'Oswald',sans-serif;font-weight:300;font-size:24px;color:var(--ink);padding-top:56px}
.features{position:absolute;left:87px;top:132px;width:761px;display:grid;grid-template-columns:401px 360px;row-gap:26px}
.feature{display:flex;gap:18px;height:92px}
.feature svg{width:78px;height:72px;flex:none}
.feature h3{font-size:14px;font-weight:500;color:var(--ink);margin-top:6px}
.feature p{font-size:10.2px;line-height:17.5px;margin-top:8px;width:270px}
.family{position:relative;height:573px}
.family .photo{left:87px;top:72px;width:366px;height:421px;background:linear-gradient(180deg,#3f4c2e 0%,#5d6b3b 40%,#6f7d3e 75%,#86933f 100%)}
.family .copy{left:503px;top:104px;width:350px;position:absolute}
.info-band{position:relative;height:174px;background:var(--teal);text-align:center;color:var(--white);font-weight:700;font-size:14.4px;line-height:28px;padding-top:38px}
.info-band .scallop{bottom:-10px;z-index:2}
</style>
</head>
<body>

<section class="page page--landing">
  <div class="topbar">
    <span><svg viewBox="0 0 10 10"><circle cx="5" cy="5" r="4.2" fill="none" stroke="#fff" stroke-width="1.3"/><path d="M5 2.5V5h2" stroke="#fff" stroke-width="1.1" fill="none"/></svg>Saturdays at Gumleaf Gully Markets: 9:00am – 2:00pm</span>
    <div class="contact">
      <span><svg viewBox="0 0 10 10"><path d="M2 0.8l1.8 2-1 1.2c.7 1.4 1.8 2.5 3.2 3.2l1.2-1 2 1.8-1.2 1.6C4.5 9.4.6 5.5.4 2z"/></svg>Call us: (02) 5550 1234</span>
      <span><svg viewBox="0 0 10 10"><rect x="0.5" y="2" width="9" height="6.5"/></svg>hello@markethaus.example</span>
    </div>
  </div>
  <header class="header">
    <div class="brand"><i></i>MARKETHAUS</div>
    <nav class="nav">
      <a>Home</a><a>About Us</a><a>Book A Stall</a><a>Stallfinder</a>
      <a class="active caret">Gumleaf Gully Markets</a><a class="caret">Ridgeview Markets</a><a>Contact Us</a>
      <svg viewBox="0 0 12 12"><circle cx="5" cy="5" r="3.6" fill="none" stroke="#111" stroke-width="1.6"/><path d="M7.7 7.7L11 11" stroke="#111" stroke-width="1.8"/></svg>
    </nav>
  </header>
  <div class="chooser">
    <h1><b>GUMLEAF GULLY</b> MARKETS</h1>
    <div class="buttons">
      <a class="pill pill--visitors"><i></i><span>VISITORS</span></a>
      <a class="pill pill--stall"><i></i><span>STALLHOLDERS</span></a>
    </div>
    <div class="scallop scallop--down-wash"></div>
  </div>
  <footer class="footer">
    <div class="footer-cols">
      <div class="f-brand"><i></i>MARKETHAUS</div>
      <div class="socials"><i></i><i></i><i></i><i></i></div>
      <div class="f-office">
        <h4>Our Office Address</h4>
        <div class="row"><svg viewBox="0 0 10 10"><path d="M2 0.8l1.8 2-1 1.2c.7 1.4 1.8 2.5 3.2 3.2l1.2-1 2 1.8-1.2 1.6C4.5 9.4.6 5.5.4 2z"/></svg><div><small>Phone</small>(02) 5550 1234</div></div>
        <div class="row"><svg viewBox="0 0 10 10"><rect x="0.5" y="2" width="9" height="6.5"/></svg><div><small>Email</small>hello@markethaus.example</div></div>
        <div class="row"><svg viewBox="0 0 10 10"><circle cx="5" cy="5" r="4" fill="none" stroke="#00BBA5" stroke-width="1.3"/></svg><div><small>Opening Hours</small>Saturdays at Gumleaf : 9:00am – 2:00pm<br>Sun at Ridgeview : 6:30am – 2:00pm</div></div>
      </div>
      <div class="f-company">
        <h4>Company</h4>
        <a>Home</a><a>About Us</a><a>Book A Stall</a><a>Stallfinder</a><a>Gumleaf Gully Markets</a><a>Ridgeview Markets</a>
      </div>
      <div class="f-quote">
        <h4>Stil have questios?</h4>
        <p>Contact us using this form. A representative will aswer your questions as soon as possible.</p>
        <span class="btn-quote">GET A QUOTE</span>
      </div>
    </div>
    <div class="rule"></div>
    <div class="goup">↑ Go Up</div>
    <div class="legal"><span>© 2021 MARKETHAUS. | All Rights Reserved</span><nav><a>Privacy Policy</a>|<a>Cookie Policy</a>|<a>Terms Of Services</a></nav></div>
  </footer>
</section>

<section class="page page--visitors">
  <div class="topbar">
    <span><svg viewBox="0 0 10 10"><circle cx="5" cy="5" r="4.2" fill="none" stroke="#fff" stroke-width="1.3"/><path d="M5 2.5V5h2" stroke="#fff" stroke-width="1.1" fill="none"/></svg>Saturdays at Gumleaf Gully Markets: 9:00am – 2:00pm</span>
    <div class="contact">
      <span><svg viewBox="0 0 10 10"><path d="M2 0.8l1.8 2-1 1.2c.7 1.4 1.8 2.5 3.2 3.2l1.2-1 2 1.8-1.2 1.6C4.5 9.4.6 5.5.4 2z"/></svg>Call us: (02) 5550 1234</span>
      <span><svg viewBox="0 0 10 10"><rect x="0.5" y="2" width="9" height="6.5"/></svg>hello@markethaus.example</span>
    </div>
  </div>
  <header class="header">
    <div class="brand"><i></i>MARKETHAUS</div>
    <nav class="nav">
      <a>Home</a><a>About Us</a><a>Book A Stall</a><a>Stallfinder</a>
      <a class="active caret">Gumleaf Gully Markets</a><a class="caret">Ridgeview Markets</a><a>Contact Us</a>
      <svg viewBox="0 0 12 12"><circle cx="5" cy="5" r="3.6" fill="none" stroke="#111" stroke-width="1.6"/><path d="M7.7 7.7L11 11" stroke="#111" stroke-width="1.8"/></svg>
    </nav>
  </header>

  <div class="visitor-hero" role="img" aria-label="Photo of shoppers walking between market stalls and food tents">
    <h1><b>GUMLEAF GULLY MARKETS</b> VISITOR INFO</h1>
    <div class="scallop scallop--down-white"></div>
  </div>

  <div class="intro">
    <div class="copy">
      <h2 class="h2">LOVE A GOOD SATURDAY MARKET?</h2>
      <p>Then you need to go to the Gumleaf Gully Markets.</p>
      <p>Are markets your idea of fun? Want to take the family somewhere that is rich in culture, choice and variety every week of the year?</p>
      <p>Uncover the secret gem of the Western <a>Riverbend Parklands</a> of Greenvale. Set in lush surroundings in a hub of activity and entertainment are variety goods galore. There's a wonderful selection of fashion, household items, homewares, handmade craft items and more awaiting you.</p>
      <p>Plus, you'll find a feast of farm fresh produce, artisan foods and all kinds of eclectic favourites in the one place. We attract family favourites across Asian, Middle Eastern and European cuisines and bring them together with products direct from the producers of Western Riverbend.</p>
      <p class="lead">This is a place for you to meet, eat and find a special treat all at the Gumleaf Gully Markets!</p>
    </div>
    <div class="photo" role="img" aria-label="Photo of visitors strolling past market tents under tall trees"></div>
  </div>

  <div class="expect">
    <div class="scallop scallop--up-wash"></div>
    <h2 class="section-title"><b>WHAT YOU CAN EXPECT</b> AT THE GUMLEAF GULLY:</h2>
    <div class="features">
      <div class="feature">
        <svg viewBox="0 0 78 72" role="img" aria-label="Food and coffee icon"><path d="M39 3C60 3 76 20 75 40 74 60 58 70 39 69 19 68 3 58 3 39 3 19 18 3 39 3z" fill="var(--orange)"/></svg>
        <div><h3>Food and Coffee</h3><p>Grab a bite and a coffee before, during or after your shopping. We'll have a variety of cuisines and coffee choices available,</p></div>
      </div>
      <div class="feature">
        <svg viewBox="0 0 78 72" role="img" aria-label="Kids fashion icon"><path d="M39 3C60 3 76 20 75 40 74 60 58 70 39 69 19 68 3 58 3 39 3 19 18 3 39 3z" fill="var(--teal)"/></svg>
        <div><h3>Kid's fashion</h3><p>Shop until you drop at Western Riverbend's newest kid's clothing location. Forget running all over town or paying hipster chic prices. Find your kid's fashion here</p></div>
      </div>
      <div class="feature">
        <svg viewBox="0 0 78 72" role="img" aria-label="Crafts icon"><path d="M39 3C60 3 76 20 75 40 74 60 58 70 39 69 19 68 3 58 3 39 3 19 18 3 39 3z" fill="var(--teal)"/></svg>
        <div><h3>Get crafty</h3><p>Nothing beats the beauty and design of quality handmade items. Uncover arts and crafts for all occasions, lovingly made knitwear, patchwork and more</p></div>
      </div>
      <div class="feature">
        <svg viewBox="0 0 78 72" role="img" aria-label="Pet friendly icon"><path d="M39 3C60 3 76 20 75 40 74 60 58 70 39 69 19 68 3 58 3 39 3 19 18 3 39 3z" fill="var(--orange)"/></svg>
        <div><h3>Pet Friendly</h3><p>Bring your furry friends for a frolick through the sprawling Western Riverbend Parklands, while picking up a treat from one of the pet stalls.</p></div>
      </div>
      <div class="feature">
        <svg viewBox="0 0 78 72" role="img" aria-label="Kids playground icon"><path d="M39 3C60 3 76 20 75 40 74 60 58 70 39 69 19 68 3 58 3 39 3 19 18 3 39 3z" fill="var(--orange)"/></svg>
        <div><h3>Fun for the kids</h3><p>Bring the kids to enjoy pony rides, a jumping castle and face painting every Saturday.</p></div>
      </div>
      <div class="feature">
        <svg viewBox="0 0 78 72" role="img" aria-label="Gourmet produce icon"><path d="M39 3C60 3 76 20 75 40 74 60 58 70 39 69 19 68 3 58 3 39 3 19 18 3 39 3z" fill="var(--teal)"/></svg>
        <div><h3>Gourmet Produce</h3><p>Shop a range of quality, gourmet produce and baked goods from olives and preserved lemons, to breads and brownies.</p></div>
      </div>
    </div>
  </div>

  <div class="family">
    <div class="photo" role="img" aria-label="Photo of a child on a pony ride on the grass"></div>
    <div class="copy">
      <h2 class="h2">WE ARE FAMILY-FRIENDLY FUN</h2>
      <p>Where else can you meet your neighbours, find items at op shop prices,meet the farmer and the food maker, all while keeping the whole family entertained?</p>
      <p>Our markets held in the glorious Western Riverbend Parklands, an oasis of greenery and community in the City of Wattleford. You can spend the day browsing fashion, handmade craft items, bric-a-brac, toys, fantastic produce and food from around the globe. Op shop through items new and old with your family every weekend.</p>
      <p>It's an ever-changing variety of options. 50% of our market stalls change on a week by week basis, so you can always find a new treasure.</p>
      <p>The Western Riverbend Parklands are there for you to enjoy. There's live entertainment, special events, food festivals and more held on the grounds. You can come for the op shopping and retail therapy and picnic and relax later with a stroll about the Parklands.</p>
    </div>
  </div>

  <div class="info-band">
    Gumleaf Gully markets are open every Saturday from 9am to 2pm.<br>
    Enter via Wattle Rd and the Banksia Drive for parking.<br>
    Public transport is available via a bus stop at the Gumleaf Gully entrance.
    <div class="scallop scallop--down-teal"></div>
  </div>

  <footer class="footer">
    <div class="footer-cols">
      <div class="f-brand"><i></i>MARKETHAUS</div>
      <div class="socials"><i></i><i></i><i></i><i></i></div>
      <div class="f-office">
        <h4>Our Office Address</h4>
        <div class="row"><svg viewBox="0 0 10 10"><path d="M2 0.8l1.8 2-1 1.2c.7 1.4 1.8 2.5 3.2 3.2l1.2-1 2 1.8-1.2 1.6C4.5 9.4.6 5.5.4 2z"/></svg><div><small>Phone</small>(02) 5550 1234</div></div>
        <div class="row"><svg viewBox="0 0 10 10"><rect x="0.5" y="2" width="9" height="6.5"/></svg><div><small>Email</small>hello@markethaus.example</div></div>
        <div class="row"><svg viewBox="0 0 10 10"><circle cx="5" cy="5" r="4" fill="none" stroke="#00BBA5" stroke-width="1.3"/></svg><div><small>Opening Hours</small>Saturdays at Gumleaf : 9:00am – 2:00pm<br>Sun at Ridgeview : 6:30am – 2:00pm</div></div>
      </div>
      <div class="f-company">
        <h4>Company</h4>
        <a>Home</a><a>About Us</a><a>Book A Stall</a><a>Stallfinder</a><a>Gumleaf Gully Markets</a><a>Ridgeview Markets</a>
      </div>
      <div class="f-quote">
        <h4>Stil have questios?</h4>
        <p>Contact us using this form. A representative will aswer your questions as soon as possible.</p>
        <span class="btn-quote">GET A QUOTE</span>
      </div>
    </div>
    <div class="rule"></div>
    <div class="goup">↑ Go Up</div>
    <div class="legal"><span>© 2021 MARKETHAUS. | All Rights Reserved</span><nav><a>Privacy Policy</a>|<a>Cookie Policy</a>|<a>Terms Of Services</a></nav></div>
  </footer>
</section>

</body>
</html>
```